Professional & attention grabbing.

A business card design, front and back. I already have a logo I will attach, but I am open to something new as well.
Things to include:
Name:
Title:
Phone:
Email:
Wanting something that is professional but attention grabbing.
Also we do a lot of work using drones on natural gas pipelines (leading the future)if you want to include any of that. I'm open to ideas.
Target Market(s)
Natural gas transmission industry / greenhouse gas mitigation industry
Industry/Entity Type
Business
Colors
Designer to choose colors to be used in the design.
Look and feel
Each slider illustrates characteristics of the customer's brand and the style your logo design should communicate.

```html
<!DOCTYPE html>
<html lang="en">
<head>
<meta charset="utf-8">
<title>Vantage Line Inspections — Business Card</title>
<link rel="stylesheet" href="https://fonts.googleapis.com/css2?family=Open+Sans:wght@400;600;700&display=swap">
<style>
  :root {
    --brand-red: #c02027;
    --ink: #1f1f1f;
    --paper: #ffffff;
    --backdrop: #ecebe8;
    --card-shadow: rgba(0, 0, 0, 0.18);
  }
  * { margin: 0; padding: 0; box-sizing: border-box; }
  html, body {
    width: 1200px;
    height: 1000px;
    overflow: hidden;
    background: var(--backdrop);
    font-family: "Open Sans", Arial, sans-serif;
  }
  .canvas { position: relative; width: 1200px; height: 1000px; }
  .card {
    position: absolute;
    left: 266px;
    width: 666px;
    height: 397px;
    box-shadow: 0 4px 14px var(--card-shadow);
  }
  .card--front { top: 74px; background: var(--paper); }
  .card--back { top: 534px; background: var(--brand-red); }

  /* front: brand block */
  .front-brand {
    position: absolute;
    left: 97px;
    top: 102px;
    display: flex;
    flex-direction: column;
    gap: 14px;
  }
  .front-brand__mark {
    width: 60px;
    height: 60px;
    background: var(--ink);
  }
  .front-brand__name {
    color: var(--brand-red);
    font-weight: 700;
    font-size: 26px;
    line-height: 1.15;
    letter-spacing: 0.5px;
  }

  /* front: contact details */
  .details {
    position: absolute;
    left: 367px;
    top: 98px;
    color: var(--ink);
    font-size: 16px;
    line-height: 25px;
  }
  .details__name {
    color: var(--brand-red);
    font-size: 21px;
    font-weight: 600;
    line-height: 28px;
    letter-spacing: 0.3px;
  }
  .details__title { margin-bottom: 17px; }
  .details__address { margin-bottom: 8px; }
  .contact-line { display: flex; align-items: center; gap: 8px; }
  .contact-line svg { width: 14px; height: 14px; flex: none; fill: var(--brand-red); }

  /* back: brand lockup */
  .back-brand {
    position: absolute;
    left: 130px;
    top: 123px;
    display: flex;
    align-items: center;
    gap: 32px;
  }
  .back-brand__mark {
    width: 147px;
    height: 151px;
    background: var(--paper);
  }
  .back-brand__name {
    color: var(--paper);
    font-weight: 700;
    font-size: 58px;
    line-height: 1;
    letter-spacing: 1px;
  }
</style>
</head>
<body>
<main class="canvas">

  <section class="card card--front" aria-label="Card front">
    <div class="front-brand">
      <div class="front-brand__mark"></div>
      <div class="front-brand__name">VANTAGE<br>LINE</div>
    </div>

    <div class="details">
      <p class="details__name">DANIEL MORROW</p>
      <p class="details__title">Managing Director</p>
      <p class="details__address">418 Harlow Ridge Road<br>Easton, PA 18042</p>
      <p class="contact-line">
        <svg viewBox="0 0 16 16" aria-hidden="true"><path d="M2 5c0-2 2-3 6-3s6 1 6 3v1h-3V5H5v1H2z M4 7h8l2 6H2z M8 8.5a2 2 0 1 0 0 4a2 2 0 1 0 0-4z"/></svg>
        + 000 000 0000
      </p>
      <p class="contact-line">
        <svg viewBox="0 0 16 16" aria-hidden="true"><path d="M1 3h14v10H1z M2 4l6 5l6-5" stroke="#fff" stroke-width="1.2"/></svg>
        info@vantageline.com
      </p>
      <p class="contact-line">
        <svg viewBox="0 0 16 16" aria-hidden="true"><path d="M8 1a7 7 0 1 0 0 14A7 7 0 0 0 8 1z M8 2.5c1 1.2 1.6 3.3 1.6 5.5S9 12.3 8 13.5C7 12.3 6.4 10.2 6.4 8S7 3.7 8 2.5z M2.5 7.3h11v1.4h-11z" fill-rule="evenodd"/></svg>
        www.vantageline.com
      </p>
    </div>
  </section>

  <section class="card card--back" aria-label="Card back">
    <div class="back-brand">
      <div class="back-brand__mark"></div>
      <div class="back-brand__name">VANTAGE<br>LINE</div>
    </div>
  </section>

</main>
</body>
</html>
```